Business Card Design

We need a business card designed for our new company. Prefer a black card with white logo & writing.

Contact Information for Business Card

Ted Galloway, address: 7-4812 Fernhollow Road, Abbotsford, BC, V3K 8R2, Office Phone: 604-712-3390, Cell: 604-947-2164, Email: ted@resinworkshub.ca

Colors

Designer to choose only greyscale colors for use in the design.

```html
<!DOCTYPE html>
<html lang="en">
<head>
<meta charset="utf-8">
<title>Resinworks Hub – Business Card</title>
<link href="https://fonts.googleapis.com/css2?family=Montserrat:wght@400;700&display=swap" rel="stylesheet">
<style>
  :root {
    --backdrop: #1d1d1d;
    --card: #000000;
    --ink: #ffffff;
  }
  * { margin: 0; padding: 0; box-sizing: border-box; }
  html, body { width: 1200px; height: 900px; overflow: hidden; }
  body {
    position: relative;
    background: var(--backdrop);
    font-family: "Montserrat", Arial, sans-serif;
    color: var(--ink);
  }
  .card {
    position: absolute;
    left: 341px;
    width: 518px;
    height: 296px;
    background: var(--card);
  }
  .card--front { top: 141px; }
  .card--back { top: 463px; display: flex; align-items: center; justify-content: center; }

  .wordmark {
    font-weight: 700;
    letter-spacing: 0.02em;
    white-space: nowrap;
    text-align: center;
  }
  .card--front .wordmark {
    position: absolute;
    top: 72px;
    left: 0; right: 0;
    font-size: 18px;
  }
  .card--back .wordmark { font-size: 28px; }

  .holder {
    position: absolute;
    left: 0; right: 0;
    top: 156px;
    text-align: center;
  }
  .holder__name { font-size: 22px; font-weight: 700; line-height: 1.2; }
  .holder__email { font-size: 13px; font-weight: 400; margin-top: 1px; }

  .contact {
    position: absolute;
    top: 218px;
    left: 0; right: 0;
    display: flex;
    justify-content: center;
    font-size: 13.5px;
    line-height: 18px;
  }
  .contact__lines {
    width: 259px;
    padding-right: 18px;
    text-align: right;
  }
  .contact__line { display: flex; justify-content: flex-end; align-items: center; gap: 6px; }
  .contact__line svg { width: 12px; height: 12px; flex: none; }
  .contact__divider { width: 1.5px; height: 50px; background: var(--ink); margin-top: 2px; }
  .contact__address { width: 259px; padding-left: 19px; }
  .contact__company { font-weight: 700; }
</style>
</head>
<body>
  <section class="card card--front">
    <div class="wordmark">RESINWORKS HUB</div>
    <div class="holder">
      <div class="holder__name">TED GALLOWAY</div>
      <div class="holder__email">ted@resinworkshub.ca</div>
    </div>
    <div class="contact">
      <div class="contact__lines">
        <div class="contact__line">604-712-3390
          <svg viewBox="0 0 24 24" fill="currentColor" aria-hidden="true"><path d="M6.6 10.8a15.1 15.1 0 0 0 6.6 6.6l2.2-2.2a1 1 0 0 1 1-.25 11.4 11.4 0 0 0 3.6.57 1 1 0 0 1 1 1V20a1 1 0 0 1-1 1A17 17 0 0 1 3 4a1 1 0 0 1 1-1h3.5a1 1 0 0 1 1 1c0 1.25.2 2.45.57 3.57a1 1 0 0 1-.25 1z"/></svg>
        </div>
        <div class="contact__line">604-947-2164
          <svg viewBox="0 0 24 24" fill="none" stroke="currentColor" stroke-width="2" aria-hidden="true"><rect x="6" y="2" width="12" height="20" rx="2"/><line x1="11" y1="18" x2="13" y2="18"/></svg>
        </div>
        <div class="contact__line">www.resinworkshub.ca
          <svg viewBox="0 0 24 24" fill="none" stroke="currentColor" stroke-width="1.8" aria-hidden="true"><circle cx="12" cy="12" r="10"/><ellipse cx="12" cy="12" rx="4.5" ry="10"/><line x1="2" y1="12" x2="22" y2="12"/><path d="M4 7h16M4 17h16"/></svg>
        </div>
      </div>
      <div class="contact__divider"></div>
      <div class="contact__address">
        <div class="contact__company">Resinworks Hub</div>
        <div>7-4812 Fernhollow Road</div>
        <div>Abbotsford, BC, V3K 8R2</div>
      </div>
    </div>
  </section>

  <section class="card card--back">
    <div class="wordmark">RESINWORKS HUB</div>
  </section>
</body>
</html>
```